Automotive Business Card Design

I would just like a automotive themed card. nothing too extravagant, but catchy.

needs to say something about doing roadside assistance,mobile repairs, Diesel repairs, and Fleet maintenance

it can be single sided or double sided. no preference there.

Industry/Entity Type

Automotive

Contact Information for Business Card

Dean Marlowe
phone 534 861 2093
Name: Brightpath Automotive & Diesel Repair

```html
<!DOCTYPE html>
<html lang="en">
<head>
<meta charset="UTF-8">
<title>Brightpath Automotive &amp; Diesel Repair – Business Card</title>
<link href="https://fonts.googleapis.com/css2?family=Cinzel:wght@400&family=Open+Sans:wght@400&display=swap" rel="stylesheet">
<style>
  :root {
    --page-bg: #2b2b2b;
    --card-bg: #ffffff;
    --ink: #111111;
    --parts-light: #f4f4f4;
    --parts-mid: #d9d9d9;
    --parts-accent: #d9393a;
  }
  html, body {
    margin: 0;
    padding: 0;
    width: 1200px;
    height: 900px;
    overflow: hidden;
    background: var(--page-bg);
  }
  .business-card {
    position: absolute;
    left: 75px;
    top: 150px;
    width: 1050px;
    height: 600px;
    background: var(--card-bg);
    color: var(--ink);
    box-sizing: border-box;
    overflow: hidden;
  }
  .company-name {
    position: absolute;
    left: 60px;
    top: 34px;
    margin: 0;
    font-family: "Cinzel", serif;
    font-weight: 400;
    font-size: 38px;
    letter-spacing: 1.5px;
    white-space: nowrap;
  }
  .parts-showcase {
    position: absolute;
    left: 80px;
    top: 135px;
    width: 560px;
    height: 410px;
    background:
      radial-gradient(circle at 30% 35%, rgba(217,57,58,0.18), transparent 40%),
      radial-gradient(circle at 75% 70%, rgba(217,57,58,0.16), transparent 35%),
      linear-gradient(135deg, var(--parts-light), var(--parts-mid));
  }
  .contact {
    position: absolute;
    left: 680px;
    top: 130px;
    font-family: "Open Sans", sans-serif;
  }
  .contact-name {
    margin: 0;
    font-size: 40px;
    font-weight: 400;
    line-height: 1.1;
  }
  .contact-phone {
    display: flex;
    align-items: center;
    gap: 20px;
    margin: 22px 0 0 36px;
    font-size: 24px;
  }
  .phone-icon { width: 20px; height: 20px; fill: var(--ink); }
  .services {
    position: absolute;
    left: 690px;
    top: 330px;
    width: 320px;
    font-family: "Open Sans", sans-serif;
  }
  .services-title {
    margin: 0;
    font-size: 30px;
    font-weight: 400;
  }
  .services-list {
    margin: 10px 0 0 56px;
    padding: 0 0 0 24px;
    font-size: 22px;
    line-height: 1.2;
    list-style: disc;
    white-space: nowrap;
  }
</style>
</head>
<body>
  <main class="business-card">
    <h1 class="company-name">Brightpath Automotive &amp; Diesel Repair</h1>

    <div class="parts-showcase" role="img" aria-label="Grid of car part illustrations: steering wheel, headlight bulb, safety vest, piston, speedometer, car key, battery, floor jack, side mirror, fuel can, tyre and spark plug"></div>

    <section class="contact">
      <h2 class="contact-name">Dean Marlowe</h2>
      <p class="contact-phone">
        <svg class="phone-icon" viewBox="0 0 24 24" aria-hidden="true">
          <path d="M6.6 10.8a15.1 15.1 0 0 0 6.6 6.6l2.2-2.2a1 1 0 0 1 1-.25 11.4 11.4 0 0 0 3.6.57 1 1 0 0 1 1 1V20a1 1 0 0 1-1 1A17 17 0 0 1 3 4a1 1 0 0 1 1-1h3.5a1 1 0 0 1 1 1c0 1.25.2 2.45.57 3.57a1 1 0 0 1-.25 1z"/>
        </svg>
        <span>534 861 2093</span>
      </p>
    </section>

    <section class="services">
      <h3 class="services-title">Services</h3>
      <ul class="services-list">
        <li>Roadside assistance</li>
        <li>Fleet maintenance</li>
        <li>Diesel repairs</li>
        <li>Mobile repairs</li>
      </ul>
    </section>
  </main>
</body>
</html>
```